Marlow Sail Works President Business Card Carbon fiber catamarans

Hi.. I need a new business card design.. I am the President of a high tech yacht builder. We build Carbon Fiber go fast catamarans... Maybe we use the file I am sharing to you as the back of the card.. We need to look cool and crisp ...

Target Market(s)

Affluent People who will purchase a cool yacht

Industry/Entity Type

Custom Yacht Builder

Contact Information for Business Card

Dean Pellway , President, 731.508.2164 USA

Font styles to use
Serif

Requirements
Must have
• the clean crisp cool feel
Nice to have
• clean and crisp
Should not have
• Bold ugly

```html
<!DOCTYPE html>
<html lang="en">
<head>
<meta charset="utf-8">
<title>Marlow Sail Works – Business Card</title>
<link rel="stylesheet" href="https://fonts.googleapis.com/css2?family=Arimo:wght@400&display=swap">
<style>
  :root {
    --page: #d9d9db;
    --card-black: #151517;
    --card-mid: #2a2a2d;
    --carbon-dark: #1a1a1c;
    --carbon-light: #3a3a3e;
    --silver: #d6d6d8;
    --silver-soft: #a9a9ad;
    --rule: #8a8a8e;
  }
  * { margin: 0; padding: 0; box-sizing: border-box; }
  html, body {
    width: 1200px; height: 960px; overflow: hidden;
    background: var(--page);
    font-family: "Arimo", Arial, sans-serif;
  }
  .canvas {
    width: 1200px; height: 960px;
    display: flex; flex-direction: column; align-items: center;
    justify-content: center; gap: 40px;
  }
  .card {
    width: 735px; height: 420px; position: relative; overflow: hidden;
    box-shadow: 0 10px 30px rgba(0,0,0,0.35);
  }

  /* Back side */
  .card-back { background: var(--carbon-dark); }
  .carbon-weave {
    position: absolute; inset: 0;
    background: radial-gradient(ellipse at 50% 40%, var(--carbon-light), var(--carbon-dark) 75%);
  }
  .back-brand {
    position: absolute; inset: 0;
    display: flex; align-items: center; justify-content: center; gap: 26px;
  }
  .brand-dot {
    width: 46px; height: 46px; border-radius: 50%;
    background: var(--silver);
  }
  .brand-name {
    color: var(--silver); font-weight: 400;
    font-size: 46px; letter-spacing: 6px; text-transform: uppercase;
  }

  /* Front side */
  .card-front {
    background: linear-gradient(180deg, var(--card-mid) 0%, var(--card-black) 100%);
    display: flex; align-items: center;
  }
  .front-brand {
    width: 330px; display: flex; flex-direction: column;
    align-items: center; gap: 18px;
  }
  .front-brand .brand-dot { width: 40px; height: 40px; }
  .front-brand .brand-name { font-size: 22px; letter-spacing: 4px; }
  .divider {
    width: 1px; height: 250px; background: var(--rule);
  }
  .contact { padding-left: 34px; color: var(--silver); }
  .person-name {
    font-size: 27px; letter-spacing: 1.5px; text-transform: uppercase;
  }
  .person-title { font-size: 15px; color: var(--silver-soft); margin-top: 6px; }
  .address { font-size: 17px; line-height: 1.35; margin-top: 22px; }
  .lines { list-style: none; margin-top: 18px; }
  .lines li {
    display: flex; align-items: center; gap: 12px;
    font-size: 17px; line-height: 1.5;
  }
  .lines svg { width: 14px; height: 14px; fill: none; stroke: var(--silver); stroke-width: 1.6; }
  .lines .phone-icon { fill: var(--silver); stroke: none; }
</style>
</head>
<body>
<main class="canvas">

  <section class="card card-back">
    <div class="carbon-weave" role="img" aria-label="Woven carbon fibre texture"></div>
    <div class="back-brand">
      <span class="brand-dot"></span>
      <span class="brand-name">Marlow Sail Works</span>
    </div>
  </section>

  <section class="card card-front">
    <div class="front-brand">
      <span class="brand-dot"></span>
      <span class="brand-name">Marlow Sail Works</span>
    </div>
    <div class="divider"></div>
    <div class="contact">
      <p class="person-name">Dean Pellway</p>
      <p class="person-title">President</p>
      <p class="address">4120 Harbor View Road<br>Newport, Rhode Island 02840</p>
      <ul class="lines">
        <li>
          <svg viewBox="0 0 14 14"><path class="phone-icon" d="M3 1l2.5 3-1.3 1.5c.8 1.7 2.1 3 3.8 3.8L9.5 8l3 2.5-1.5 2.3C6 13 1 8 1.2 3z"/></svg>
          731-508-2164
        </li>
        <li>
          <svg viewBox="0 0 14 14"><rect x="3.5" y="1" width="7" height="12" rx="1.2"/><line x1="6" y1="11" x2="8" y2="11"/></svg>
          731-508-3370
        </li>
        <li>
          <svg viewBox="0 0 14 14"><rect x="1" y="3" width="12" height="8"/><polyline points="1,3 7,8 13,3"/></svg>
          name@marlowsail.com
        </li>
        <li>
          <svg viewBox="0 0 14 14"><circle cx="7" cy="7" r="5.8"/><ellipse cx="7" cy="7" rx="2.4" ry="5.8"/><line x1="1.2" y1="7" x2="12.8" y2="7"/></svg>
          www.marlowsail.com
        </li>
      </ul>
    </div>
  </section>

</main>
</body>
</html>
```